Healthcare and Professional IT Services Company need a redesigned business card

We are a IT Services company that targets small medical practices and professional business such as Attorneys, Accounts, Architects etc. We want to communicate a professional yet friendly image using recent logo redesign here on ArtHarbor. Like to see the colors blue and orange in the design. Must use the Tall Pine Computing as displayed in the new logo - then also want to incorporate the fish logo as well.

Target Market(s)

Small medical and professional services

Industry/Entity Type

It Company

Contact Information for Business Card

The usual stuff, place for name address phone website. Also maybe our tagline which is "Rooted in technology"

Requirements
Must have
• My new logo and the fish somewhere on the card

```html
<!DOCTYPE html>
<html lang="en">
<head>
<meta charset="utf-8">
<title>Tall Pine Computing – Business Card</title>
<link rel="stylesheet" href="https://fonts.googleapis.com/css2?family=Open+Sans:wght@400;600;700&display=swap">
<style>
  :root {
    --backdrop: #2c2c2c;
    --backdrop-edge: #1d1d1d;
    --brand-blue: #1680c6;
    --brand-blue-deep: #0f6fb3;
    --sky-blue: #2aa9e0;
    --brand-orange: #f7a11a;
    --card-white: #ffffff;
    --ink-light: #ffffff;
  }
  * { box-sizing: border-box; margin: 0; padding: 0; }
  html, body { width: 1200px; height: 659px; overflow: hidden; }
  body {
    background: radial-gradient(ellipse at 50% 45%, var(--backdrop) 0%, var(--backdrop-edge) 100%);
    font-family: "Open Sans", Arial, sans-serif;
    position: relative;
  }
  .card {
    position: absolute;
    top: 181px;
    width: 520px;
    height: 297px;
    overflow: hidden;
    border-radius: 2px;
    box-shadow: 0 10px 24px rgba(0,0,0,.45);
  }
  .card--front { left: 50px; background: var(--card-white); }
  .card--back {
    left: 630px;
    background: linear-gradient(160deg, var(--brand-blue) 0%, var(--brand-blue-deep) 100%);
  }
  .card__shapes { position: absolute; inset: 0; }

  /* Front */
  .identity {
    position: absolute;
    left: 38px;
    top: 78px;
    width: 230px;
  }
  .identity__mascot {
    width: 96px;
    height: 70px;
    border-radius: 40% 50% 45% 40%;
    background: linear-gradient(135deg, #d8effa 0%, #9fd6f1 100%);
    margin-bottom: 12px;
  }
  .identity__wordmark {
    font-size: 20px;
    font-weight: 700;
    color: var(--sky-blue);
    letter-spacing: .2px;
    line-height: 1.1;
  }
  .identity__name {
    margin-top: 16px;
    font-size: 14px;
    font-weight: 600;
    color: var(--sky-blue);
  }
  .identity__title {
    font-size: 12px;
    color: var(--brand-orange);
    margin-top: 2px;
  }
  .contact {
    position: absolute;
    right: 22px;
    top: 42px;
    list-style: none;
    text-align: right;
    color: var(--ink-light);
    font-size: 11px;
    line-height: 19px;
  }
  .contact__item { display: flex; justify-content: flex-end; align-items: center; gap: 8px; }
  .contact__item--gap { margin-top: 14px; }
  .contact__icon { width: 11px; height: 11px; flex: none; }
  .contact__spacer { width: 11px; flex: none; }

  /* Back */
  .back__mascot {
    position: absolute;
    left: 22px;
    top: -20px;
    width: 290px;
    height: 220px;
    border-radius: 45% 55% 50% 45%;
    background: linear-gradient(140deg, rgba(255,255,255,.28) 0%, rgba(255,255,255,.12) 100%);
  }
  .back__brand {
    position: absolute;
    right: 28px;
    bottom: 34px;
    text-align: right;
    color: var(--ink-light);
  }
  .back__wordmark { font-size: 26px; font-weight: 700; line-height: 1.1; }
  .back__tagline { font-size: 13px; margin-top: 6px; letter-spacing: .3px; }
</style>
</head>
<body>

  <section class="card card--front" aria-label="Business card front">
    <svg class="card__shapes" viewBox="0 0 520 297" aria-hidden="true">
      <path d="M268 0 Q372 140 338 297 L520 297 L520 0 Z" fill="var(--brand-orange)"/>
      <path d="M288 0 Q392 140 358 297 L520 297 L520 0 Z" fill="var(--brand-blue)"/>
      <path d="M252 0 Q356 140 322 297" fill="none" stroke="var(--sky-blue)" stroke-width="4"/>
    </svg>

    <div class="identity">
      <div class="identity__mascot" role="img" aria-label="Friendly cartoon mascot illustration"></div>
      <p class="identity__wordmark">Tall Pine Computing</p>
      <p class="identity__name">Dana Reyes</p>
      <p class="identity__title">CEO/Founder</p>
    </div>

    <ul class="contact">
      <li class="contact__item"><span>412 Cedar Row</span><span class="contact__spacer"></span></li>
      <li class="contact__item"><span>Juneau, Alaska 99801</span>
        <svg class="contact__icon" viewBox="0 0 12 12" aria-hidden="true"><path d="M6 1a3.5 3.5 0 0 0-3.5 3.5C2.5 7 6 11 6 11s3.5-4 3.5-6.5A3.5 3.5 0 0 0 6 1Zm0 5a1.4 1.4 0 1 1 0-2.8A1.4 1.4 0 0 1 6 6Z" fill="#fff"/></svg>
      </li>
      <li class="contact__item"><span>555 014 2290</span>
        <svg class="contact__icon" viewBox="0 0 12 12" aria-hidden="true"><path d="M3 1l2 2.6-1.2 1.2a7 7 0 0 0 3.4 3.4L8.4 7 11 9l-1.4 2C5 11 1 7 1 2.4Z" fill="#fff"/></svg>
      </li>
      <li class="contact__item contact__item--gap"><span>info@tallpine.net</span>
        <svg class="contact__icon" viewBox="0 0 12 12" aria-hidden="true"><rect x="1" y="2.5" width="10" height="7" rx="1" fill="#fff"/><path d="M1.5 3.2 6 6.5l4.5-3.3" fill="none" stroke="var(--brand-blue)" stroke-width="1"/></svg>
      </li>
      <li class="contact__item"><span>www.tallpine.net</span>
        <svg class="contact__icon" viewBox="0 0 12 12" aria-hidden="true"><circle cx="6" cy="6" r="5" fill="#fff"/><path d="M1 6h10M6 1c2 2.5 2 7.5 0 10M6 1c-2 2.5-2 7.5 0 10" fill="none" stroke="var(--brand-blue)" stroke-width=".8"/></svg>
      </li>
    </ul>
  </section>

  <section class="card card--back" aria-label="Business card back">
    <div class="back__mascot" role="img" aria-label="Large outlined mascot illustration"></div>
    <div class="back__brand">
      <p class="back__wordmark">Tall Pine Computing</p>
      <p class="back__tagline">Rooted in technology</p>
    </div>
  </section>

</body>
</html>
```